A tri fold flyer to be sent to parents advertising Learning Center, tutoring in math or language after school and on weekendsSince 1994 the Bright Owl Study House has been helping the children on Oahu do better in school. Bright Owl has developed a successful method of teaching math, reading and writing for students in grades K-12. Affordable and effective, it's unlike any other learning system.

Target Market(s)

Parents of school age kids

Industry/Entity Type

Education

Font styles to use
Sans Serif

Requirements
Must have
• same text as in previews
Nice to have
• 3 fold
Should not have
• mistakes

```html
<!DOCTYPE html>
<html lang="en">
<head>
<meta charset="utf-8">
<title>Bright Owl Study House – Tri-fold Flyer</title>
<link rel="stylesheet" href="https://fonts.googleapis.com/css2?family=Questrial&display=swap">
<style>
  :root {
    --page-bg: #dcdcdc;
    --teal: #5cbdbd;
    --teal-deep: #1ea5b6;
    --teal-mist: #e4f4f3;
    --green: #8cc63f;
    --orange: #f0a43c;
    --orange-deep: #ec8a24;
    --blue: #2f8fe0;
    --yellow: #f6d000;
    --white: #ffffff;
    --ink-teal: #1f9fae;
    --photo-warm: #b9a58f;
    --photo-cool: #6f8fb8;
  }
  * { box-sizing: border-box; margin: 0; padding: 0; }
  html, body {
    width: 1200px; height: 870px; overflow: hidden;
    background: var(--page-bg);
    font-family: "Questrial", "Helvetica Neue", Arial, sans-serif;
  }
  .flyer {
    position: absolute; left: 54px; top: 13px;
    width: 1092px; height: 844px;
    display: flex;
    box-shadow: 0 6px 20px rgba(0,0,0,.18);
  }
  .panel { position: relative; width: 364px; height: 844px; overflow: hidden; }
  .panel + .panel { border-left: 1px solid rgba(0,0,0,.06); }
  .panel-art { position: absolute; inset: 0; width: 364px; height: 844px; }
  .copy { position: absolute; left: 30px; right: 30px; color: var(--white); font-size: 13.5px; line-height: 1.42; }
  .copy p { text-align: justify; margin-bottom: 12px; }

  /* panel: what we do */
  .intro-title { position: absolute; left: 30px; top: 44px; color: var(--ink-teal); }
  .intro-title h2 { font-size: 27px; font-weight: 400; letter-spacing: .5px; }
  .intro-title p { font-size: 17px; line-height: 1.1; margin-top: 4px; width: 180px; }
  .subject { position: absolute; width: 64px; height: 50px; border-radius: 50%;
    color: var(--white); font-size: 10px; line-height: 1.05; text-align: center;
    display: flex; align-items: center; justify-content: center; }
  .subject--language { left: 262px; top: 18px; background: var(--blue); }
  .subject--math { left: 272px; top: 74px; background: var(--orange); font-size: 12px; }
  .subject--ssat { left: 282px; top: 130px; background: var(--yellow); }
  .intro-copy { top: 330px; }
  .site-url { position: absolute; left: 0; right: 0; bottom: 22px; text-align: center;
    color: #4a5a5a; font-size: 17px; letter-spacing: .6px; }

  /* panel: tutoring */
  .tutoring-copy { top: 318px; }
  .tutoring-copy h3 { font-size: 17px; font-weight: 400; letter-spacing: .3px; }
  .tutoring-copy .tagline { font-size: 15px; margin-bottom: 16px; text-align: left; }
  .lesson-note { top: 752px; font-size: 14px; }

  /* panel: better way */
  .method-copy { top: 34px; }
  .method-copy h3, .schedule-copy h3 { font-size: 16px; font-weight: 400; margin-bottom: 10px; }
  .schedule-copy { top: 636px; }
</style>
</head>
<body>
<main class="flyer">

  <!-- panel 1 -->
  <section class="panel panel--intro">
    <svg class="panel-art" viewBox="0 0 364 844" aria-hidden="false">
      <rect width="364" height="844" fill="var(--teal-mist)"/>
      <path d="M0,300 C130,305 270,255 364,150 L364,844 L0,844 Z" fill="var(--teal)"/>
      <path d="M0,598 C120,560 250,520 364,535 L364,548 C250,536 120,575 0,612 Z" fill="var(--green)"/>
      <g role="img" aria-label="Group photo of smiling students in matching blue shirts">
        <path d="M0,612 C120,575 250,536 364,548 L364,765 C250,742 120,758 0,800 Z" fill="var(--photo-cool)"/>
      </g>
      <path d="M0,800 C120,758 250,742 364,765 L364,844 L0,844 Z" fill="var(--white)"/>
      <path d="M110,790 C200,760 290,758 364,775 L364,786 C290,772 200,774 110,790 Z" fill="var(--green)"/>
      <path d="M0,830 C120,800 250,790 364,805 L364,844 L0,844 Z" fill="var(--teal-mist)"/>
    </svg>
    <div class="intro-title">
      <h2>WHAT WE DO</h2>
      <p>Personalized instruction makes learning fun!</p>
    </div>
    <div class="subject subject--language">language<br>arts</div>
    <div class="subject subject--math">math</div>
    <div class="subject subject--ssat">SSAT<br>preparation</div>
    <div class="copy intro-copy">
      <p>Since 1994 the Bright Owl Study House has been helping the children on Oahu do better in school.</p>
      <p>Bright Owl has developed a successful method of teaching math, reading and writing for students in grades K-12.</p>
      <p>Affordable and effective, it's unlike any other learning system.</p>
    </div>
    <div class="site-url">www.brightowlstudy.com</div>
  </section>

  <!-- panel 2 -->
  <section class="panel panel--tutoring">
    <svg class="panel-art" viewBox="0 0 364 844">
      <rect width="364" height="844" fill="var(--teal-mist)"/>
      <g role="img" aria-label="Photo of a teacher giving a young student a high five in class">
        <path d="M40,60 C60,30 200,20 364,22 L364,250 C250,262 130,290 40,300 Z" fill="var(--photo-warm)"/>
      </g>
      <path d="M0,40 C60,20 200,5 364,10 L364,22 C200,18 60,30 0,52 Z" fill="var(--green)"/>
      <path d="M0,300 C120,285 250,250 364,235 L364,844 L0,844 Z" fill="var(--teal)"/>
      <path d="M150,285 C230,262 300,250 364,248 L364,262 C300,262 230,272 150,285 Z" fill="var(--green)"/>
      <path d="M0,735 C130,715 260,705 364,712 L364,844 L0,844 Z" fill="var(--teal-deep)"/>
    </svg>
    <div class="copy tutoring-copy">
      <h3>MORE THAN JUST TUTORING...</h3>
      <p class="tagline">It's a better way of learning</p>
      <p>Rather than simply walking students through worksheets or a being a homework assistant, Bright Owl is a productive and exciting way to learn.</p>
      <p>Lessons are designed to accommodate students at any ability level. All students (remedial, average and gifted) benefit because the programs are personalized.</p>
      <p>Pre and post test measure the student's progress. Outstanding improvement is made because every lesson is designed to challenge the student while ensuring that a specific skill is mastered.</p>
    </div>
    <div class="copy lesson-note">
      <p>Lessons are an extended hour long (70 minutes), most kids come twice a week; the charge is $35 per lesson.</p>
    </div>
  </section>

  <!-- panel 3 -->
  <section class="panel panel--method">
    <svg class="panel-art" viewBox="0 0 364 844">
      <defs>
        <linearGradient id="orangeFade" x1="0" y1="0" x2="1" y2="1">
          <stop offset="0" stop-color="var(--orange)"/>
          <stop offset="1" stop-color="var(--orange-deep)"/>
        </linearGradient>
      </defs>
      <rect width="364" height="844" fill="url(#orangeFade)"/>
      <path d="M0,330 C120,310 250,285 364,270 L364,610 C250,600 120,615 0,640 Z" fill="var(--teal-deep)"/>
      <g role="img" aria-label="Photo of a teenage student writing at a desk near a bookshelf">
        <path d="M0,350 C120,330 250,305 364,295 L364,585 C250,575 120,590 0,615 Z" fill="var(--photo-warm)"/>
      </g>
      <path d="M0,615 C120,590 250,575 364,585 L364,600 C250,592 120,605 0,628 Z" fill="var(--teal-mist)"/>
    </svg>
    <div class="copy method-copy">
      <h3>It really is a better way of learning...</h3>
      <p>Each lesson has a variety of learning activities, which include personalized instruction, hands on manipulatives and individual computer sessions.</p>
      <p>This multisensory method of instruction provides the maximum amount of learning in the minimum amount of time.</p>
      <p>Bright Owl students have experiences of being successful, which builds their confidence.</p>
    </div>
    <div class="copy schedule-copy">
      <h3>Two lessons a week can make a big difference.</h3>
      <p>We offer lessons Monday – Saturday year round. This is our basic schedule. On school days, the first lesson is at 2:30. When you register we look at both our schedule and yours to see what works for both of us.</p>
    </div>
  </section>

</main>
</body>
</html>
```